Maple Beacon Website

We are starting a marketing company and to do that we need a website! We want a website that will inspire and persuade to bring out the awesomeness in our clients.
What we want to see:
- Inspirational and persuasive imagery that relate to Branding.
- No cliche images eg. business man, suits and hand shakes
- We want to transform and educate our clients.
- We want to show them the path and would like our website to really act as a guide that guides them step by step through our process.
- We want the portray that we are an investment but not have a pretentious way to it. We put our heart into every project and that is how we treat our clients.
-When you submit your design please include what platform you have created for. Preference would be Wordpress or Joobla.

We have included the psd file for the wire frame, logo files, font files, site map and a link to a video we create to give you more information on what we would like to see. http://clipvault.example/t/qk82LmZpr

Feel free to make small modification to the logos if you think it will improve it. Your creativity and advice is most welcome.
Updates

One thing we forgot. We would like to have our contact information near the top of the website as well as at the bottom.  Here is out contact info:

Email: info@maplebeacon.example
Phone: 587-555-0142

Project Deadline Extended
Reason: As we are new with the platform and that we want to optimize our results, we decided to extend the deadline by 15 days. Thanks!

Target Market(s)

28-60, Male and Female, Oil field, Local Businesses, Dentists, Chiropractors, Hair salon, Construction/Renovation, Events etc

Industry/Entity Type

Investment

Requirements
Must have
• - 4 Inspirational and persuasive Imagery for the top portion of the website
- Must have a feel as if your not on a website an example of this is linked below.
http://www.artbidhub.example/design/402957/web-design-by-lena-torvik
Nice to have
• - Creative advice from you.
- Creative buttons for Get Free Quote and Subscribe buttons. Something out of the box that draws peoples attention. eg. a 'B' button. Just and example but still something related to branding.
Should not have
• No Cliches

```html
<!DOCTYPE html>
<html lang="en">
<head>
<meta charset="utf-8">
<title>Maple Beacon</title>
<link href="https://fonts.googleapis.com/css2?family=Source+Sans+3:ital,wght@0,400;0,600;0,700;1,400&family=Arimo:wght@400;700&family=Cinzel:wght@500&display=swap" rel="stylesheet">
<style>
:root{
  --page:#e6e6e6;
  --green:#8cc63f;
  --green-light:#b4e05a;
  --green-dark:#5f9a1e;
  --green-text:#4f8a2a;
  --ink:#333333;
  --grey-text:#8a8a8a;
  --panel-top:#ffffff;
  --panel-bottom:#e4e4e4;
  --hero-dark:#0d1418;
  --hero-blue:#3d6a8c;
  --footer:#2b2b2b;
  --white:#ffffff;
  --dot-off:#6e6e6e;
}
*{margin:0;padding:0;box-sizing:border-box}
html,body{width:1200px;height:953px;overflow:hidden}
body{background:var(--page);position:relative;font-family:"Source Sans 3",sans-serif;color:var(--ink)}
.abs{position:absolute}

.side-panel{left:35px;top:0;width:278px;height:378px;background:linear-gradient(180deg,var(--panel-top) 0%,var(--panel-bottom) 100%)}
.brand{left:59px;top:44px;display:flex;align-items:center;gap:10px}
.brand-mark{width:16px;height:16px;border-radius:50%;background:var(--green)}
.brand-name{font-size:34px;font-weight:700;color:#6a6a6a;letter-spacing:.5px;line-height:1}
.tagline{left:35px;width:278px;top:115px;text-align:center;font-style:italic;font-size:17px;color:#444}
.main-nav{left:59px;top:168px;list-style:none}
.main-nav li{font-size:21px;line-height:28px;color:#222;text-transform:uppercase}
.connect-label{left:35px;width:278px;top:334px;text-align:center;font-style:italic;font-size:28px;color:#555}

.contact-bar{left:313px;top:0;width:852px;height:68px;background:linear-gradient(180deg,var(--green-light),var(--green) 70%,var(--green-dark));border-bottom:2px solid var(--white)}
.contact-item{top:18px;display:flex;align-items:center;gap:10px;color:var(--white);font-size:15px;font-weight:600}
.contact-item svg{width:40px;height:40px}

.hero{left:313px;top:70px;width:852px;height:308px;background:radial-gradient(ellipse at 30% 55%,var(--hero-blue) 0%,#1e3346 35%,var(--hero-dark) 75%)}
.slide-nav{left:664px;top:96px;display:flex;gap:18px;list-style:none}
.slide-nav li{display:flex;align-items:center;gap:8px;font-size:17px;color:#9a9a9a}
.slide-nav li::before{content:"";width:17px;height:17px;border-radius:50%;background:var(--dot-off)}
.slide-nav li.active{color:var(--green)}
.slide-nav li.active::before{background:var(--green)}

.newsletter-band{left:35px;top:378px;width:1130px;height:51px;background:linear-gradient(180deg,var(--green-light),var(--green) 60%,var(--green-dark))}
.social-tile{top:384px;width:38px;height:38px;border-radius:6px;background:linear-gradient(180deg,#fafafa,#cfcfcf);border:1px solid #9a9a9a}
.newsletter-text{left:315px;top:389px;font-family:"Arimo",sans-serif;font-size:21px;color:var(--white)}
.subscribe-btn{left:794px;top:381px;width:171px;height:42px;border-radius:9px;background:#000;color:var(--white);font-family:"Arimo",sans-serif;font-weight:700;font-size:18px;display:flex;align-items:center;justify-content:center;border:1px solid #444}

.content-card{left:235px;top:433px;width:730px;height:365px;background:#f4f4f4;border:1px solid #cfcfcf}
.welcome{left:235px;width:730px;top:470px;text-align:center;font-size:26px;font-weight:400;color:#555;letter-spacing:-.3px}
.welcome span{color:var(--green-text)}
.copy{left:284px;width:660px;font-family:"Arimo",sans-serif;font-size:13.2px;line-height:21px;color:var(--grey-text)}
.quote-btn{left:739px;top:738px;width:202px;height:44px;border-radius:7px;background:linear-gradient(180deg,#8fd34a,#4a9a1a 55%,#3b7f12);border:1px solid #2f6a0d;box-shadow:0 2px 3px rgba(0,0,0,.35);color:var(--white);font-family:"Cinzel",serif;font-size:23px;display:flex;align-items:center;justify-content:center;gap:8px}
.quote-btn svg{width:12px;height:16px}

.site-footer{left:0;top:809px;width:1200px;height:144px;background:var(--footer);color:var(--white);font-family:"Arimo",sans-serif}
.footer-nav{left:244px;top:843px;display:flex;list-style:none;font-size:14px;color:var(--white)}
.footer-nav li+li::before{content:"/";margin:0 42px}
.footer-contact{left:243px;top:900px;font-size:14.5px;color:var(--white)}
.copyright{left:779px;top:903px;font-size:13px;color:#777}
</style>
</head>
<body>

<header>
  <div class="abs side-panel"></div>
  <div class="abs brand"><span class="brand-mark"></span><span class="brand-name">Maple Beacon</span></div>
  <p class="abs tagline">Because You´re Awesome!</p>
  <ul class="abs main-nav">
    <li>Strategy</li><li>Portfolio</li><li>About Us</li><li>Contact Us</li><li>Blog</li>
  </ul>
  <p class="abs connect-label">Connect with us!</p>

  <div class="abs contact-bar"></div>
  <div class="abs contact-item" style="left:647px">
    <svg viewBox="0 0 40 40" aria-hidden="true"><circle cx="20" cy="20" r="18" fill="#e8e8e8" stroke="#9a9a9a"/><text x="20" y="27" text-anchor="middle" font-family="Arimo,sans-serif" font-size="20" font-weight="700" fill="#555">@</text></svg>
    <span>Email: info@maplebeacon.example</span>
  </div>
  <div class="abs contact-item" style="left:940px">
    <svg viewBox="0 0 40 40" aria-hidden="true"><circle cx="20" cy="20" r="18" fill="#e8e8e8" stroke="#9a9a9a"/><path d="M14 10c-2 1-3 3-2 6 2 6 6 11 12 14 3 1 5 0 6-2l-4-4-3 2c-3-2-5-4-6-7l2-3z" fill="#555"/></svg>
    <span>Phone: 587-555-0142</span>
  </div>

  <div class="abs hero" role="img" aria-label="Branding concept imagery: brand, essence, attribute and identity sketched on a dark glass board"></div>
  <ul class="abs slide-nav">
    <li class="active">Maple Beacon</li><li>Be Found</li><li>Connect</li><li>Get Growing</li>
  </ul>

  <div class="abs newsletter-band"></div>
  <div class="abs social-tile" style="left:85px"></div>
  <div class="abs social-tile" style="left:138px"></div>
  <div class="abs social-tile" style="left:191px"></div>
  <p class="abs newsletter-text">Get Tips and Tricks! Subscribe to our Newsletter.</p>
  <div class="abs subscribe-btn">Subscribe Now</div>
</header>

<main>
  <div class="abs content-card"></div>
  <h1 class="abs welcome"><span>WELCOME TO</span> MAPLE BEACON</h1>
  <p class="abs copy" style="top:533px">This is just a bunch of words put toghether to make it look like&nbsp; paragraph. It is purly for show and filler so that we can have a general idea of what it will ook like when we put in the proper pagaraphs thatmake up our mission statment. I think this font size looks pretty good but maybe be a tad bit smaler.&nbsp; would like to see the welcome a little more dramatic looking. I think that</p>
  <p class="abs copy" style="top:639px">is all I need to write here for now. This is just a bunch of words put toghether to make it look like&nbsp; paragraph. It is purly for show and filler so that we can have a general idea of what it will ook like when we put in the proper pagaraphs thatmake up our mission statment. I think this font size looks pretty good but maybe be a tad bit smaler.&nbsp; would like to see the welcome a little more dramatic looking. I think</p>
  <div class="abs quote-btn">FREE QUOTE<svg viewBox="0 0 12 16" aria-hidden="true"><path d="M1 1l10 7-10 7z" fill="#fff"/></svg></div>
</main>

<footer class="abs site-footer"></footer>
<ul class="abs footer-nav">
  <li>Site Map</li><li>Strategy</li><li>Portfolio</li><li>About Us</li><li>Contact Us</li><li>Blog</li>
</ul>
<p class="abs footer-contact">Contact info&nbsp;&nbsp; :&nbsp; Email: info@maplebeacon.example&nbsp;&nbsp;&nbsp;&nbsp;&nbsp; Phone: 587-555-0142</p>
<p class="abs copyright">©MAPLE BEACON INC. 2013</p>

</body>
</html>
```